Independent Statistical Consultant Business Card

I will be going out as an independent statistical consultant and need a business card. I specialize in data analysis and statistics for health care and public health

I am an Chartered Quantitative Analyst from the Coastal Numerics Federation. Would like to incorporate that logo into the design

The design should be modern with classic colors, convey accuracy, analytic creativity and responsiveness to client needs.

The name of the firm will be simply Tim Halvorsen Applied Statistical Consulting

To all designers, I want to clarify that the QMetr logo and the phrase Chartered Quantitative Analyst are not the name of the company nor the focus of the card. They are equivalent to being a Velorin Qualified Engineer (VQE) but in the area of statistics The name of the firm will be: Tim Halvorsen, Applied Statistical Consulting. I look forward to your submissions. Thanks. Tim

```html
<!DOCTYPE html>
<html lang="en">
<head>
<meta charset="utf-8">
<title>Tim Halvorsen, Applied Statistical Consulting – Business Card</title>
<link rel="stylesheet" href="https://fonts.googleapis.com/css2?family=EB+Garamond:wght@400;600;700&display=swap">
<style>
  :root {
    --backdrop: #3a3a3a;
    --card: #f4f4f4;
    --brand-blue: #1f56a8;
    --ink: #333333;
    --ink-soft: #4a4a4a;
    --rule: #1a1a1a;
  }
  html, body {
    margin: 0;
    padding: 0;
    width: 1200px;
    height: 1116px;
    overflow: hidden;
    background: var(--backdrop);
  }
  .canvas {
    position: relative;
    width: 1200px;
    height: 1116px;
  }
  .card {
    position: absolute;
    left: 100px;
    top: 272px;
    width: 1000px;
    height: 572px;
    background: var(--card);
    overflow: hidden;
    font-family: "EB Garamond", Georgia, serif;
    color: var(--ink);
    box-shadow: 0 18px 40px rgba(0,0,0,0.45);
  }
  .card-bands {
    position: absolute;
    inset: 0;
  }
  .band { fill: var(--brand-blue); }
  .brand {
    position: absolute;
    left: 160px;
    top: 72px;
    width: 370px;
    text-align: center;
  }
  .brand-name {
    font-size: 104px;
    font-weight: 600;
    line-height: 1;
    letter-spacing: -1px;
    color: var(--ink);
  }
  .brand-tagline {
    margin-top: 8px;
    font-size: 26px;
    color: var(--ink-soft);
    letter-spacing: 0.3px;
    white-space: nowrap;
  }
  .divider {
    position: absolute;
    left: 552px;
    top: 236px;
    width: 3px;
    height: 200px;
    background: var(--rule);
  }
  .holder {
    position: absolute;
    left: 150px;
    top: 350px;
  }
  .holder-name {
    font-size: 36px;
    font-weight: 700;
    color: var(--brand-blue);
    text-transform: uppercase;
    letter-spacing: 0.5px;
    line-height: 1.1;
    white-space: nowrap;
  }
  .holder-firm {
    font-size: 26px;
    color: var(--ink);
    white-space: nowrap;
  }
  .contacts {
    position: absolute;
    left: 595px;
    top: 222px;
    list-style: none;
    margin: 0;
    padding: 0;
    font-size: 23px;
    color: var(--ink);
  }
  .contact-item {
    display: flex;
    align-items: center;
    gap: 12px;
    height: 34px;
    white-space: nowrap;
  }
  .contact-icon {
    width: 22px;
    height: 22px;
    fill: var(--brand-blue);
  }
  .address {
    position: absolute;
    left: 629px;
    top: 355px;
    margin: 0;
    font-style: normal;
    font-size: 23px;
    line-height: 1.25;
    color: var(--ink);
  }
</style>
</head>
<body>
<main class="canvas">
  <section class="card" aria-label="Business card">
    <svg class="card-bands" width="1000" height="572" viewBox="0 0 1000 572" aria-hidden="true">
      <path class="band band-top" d="M270,0 H1000 V16 H310 C290,16 285,0 270,0 Z"/>
      <path class="band band-bottom" d="M0,546 H780 C810,546 805,526 835,526 H1000 V572 H0 Z"/>
    </svg>

    <header class="brand">
      <div class="brand-name">QMetr</div>
      <div class="brand-tagline">Chartered Quantitative Analyst</div>
    </header>

    <div class="divider" aria-hidden="true"></div>

    <div class="holder">
      <div class="holder-name">Tim Halvorsen</div>
      <div class="holder-firm">Applied Statistical Consulting</div>
    </div>

    <ul class="contacts">
      <li class="contact-item">
        <svg class="contact-icon" viewBox="0 0 24 24" aria-label="Phone" role="img">
          <path d="M3 9c0-3 4-5 9-5s9 2 9 5v2h-5V8.5c-1.2-.5-2.6-.7-4-.7s-2.8.2-4 .7V11H3z"/>
          <path d="M6 13h12l2 7H4z"/>
        </svg>
        <span>+61 400 217 946</span>
      </li>
      <li class="contact-item">
        <svg class="contact-icon" viewBox="0 0 24 24" aria-label="Fax" role="img">
          <path d="M7 3h10v5H7z"/>
          <path d="M3 9h18v8h-3v4H6v-4H3zM8 15v4h8v-4z"/>
        </svg>
        <span>+61 400 217 900</span>
      </li>
      <li class="contact-item">
        <svg class="contact-icon" viewBox="0 0 24 24" aria-label="Email" role="img">
          <path d="M2 5h20v14H2zM4 7v.6l8 6 8-6V7zm0 3v7h16v-7l-8 6z"/>
        </svg>
        <span>tim@halvorsenstats.com</span>
      </li>
    </ul>

    <address class="address">
      48 Harbor Lane<br>
      Fairhaven, NM 87001
    </address>
  </section>
</main>
</body>
</html>
```